Process Serving Company needs a letterhead design

Looking to have a letterhead designed for letters to attorneys advertising our business. We would like something eye catching but professional. Colors and logos are attached. Please add "Process Service and Attorney Support" near the logo or header

Target Market(s)

Attorneys

Font styles to use
Serif
Sans Serif

Colors
33a6d7
0255a3
85cae6
cee9f5
ecf7fb

```html
<!DOCTYPE html>
<html lang="en">
<head>
<meta charset="utf-8">
<title>Copperline Legal Couriers Letterhead</title>
<link rel="stylesheet" href="https://fonts.googleapis.com/css2?family=Open+Sans:wght@400;600&family=Roboto:wght@400&display=swap">
<style>
  :root {
    --brand-blue: #33a6d7;
    --brand-navy: #0255a3;
    --brand-sky: #85cae6;
    --brand-mist: #cee9f5;
    --brand-ice: #ecf7fb;
    --paper: #f7f7f6;
    --backdrop: #e9e9e9;
    --ink: #555a5e;
    --ink-dark: #33373a;
    --rule: #6d7175;
  }
  * { box-sizing: border-box; margin: 0; padding: 0; }
  html, body { width: 1200px; height: 795px; overflow: hidden; }
  body { background: var(--backdrop); position: relative; }

  .letterhead {
    position: absolute; left: 319px; top: 0;
    width: 562px; height: 795px;
    background: var(--paper);
    overflow: hidden;
  }

  .brand { position: absolute; left: 52px; top: 62px; display: flex; align-items: center; gap: 7px; }
  .brand-mark { width: 10px; height: 10px; border-radius: 50%; background: var(--brand-navy); }
  .brand-name {
    font-family: "Open Sans", sans-serif; font-weight: 600; font-size: 15px;
    color: var(--brand-navy); line-height: 1;
  }

  .contact { position: absolute; left: 380px; top: 44px; padding-left: 14px; border-left: 1px solid var(--rule); font-style: normal; }
  .contact-tagline {
    font-family: "Roboto", sans-serif; font-size: 6.5px; letter-spacing: 0.4px;
    text-transform: uppercase; color: var(--brand-blue); line-height: 11px; margin-bottom: 2px;
  }
  .contact-item {
    display: flex; align-items: center; gap: 5px;
    font-family: "Roboto", sans-serif; font-size: 8.5px; color: var(--ink-dark); line-height: 13px;
  }
  .contact-item svg { width: 7px; height: 7px; fill: var(--brand-blue); flex: none; }

  .watermark {
    position: absolute; left: 420px; top: 330px; width: 130px; height: 190px;
    background: var(--brand-ice); opacity: 0.6;
  }

  .letter-body {
    position: absolute; left: 86px; top: 196px; width: 420px;
    font-family: "Open Sans", sans-serif; font-size: 9px; line-height: 14px; color: var(--ink);
  }
  .salutation { margin-bottom: 10px; }
  .letter-body p { margin-bottom: 14px; }
  .closing { margin-top: 4px; }

  .signature {
    position: absolute; left: 128px; top: 590px; width: 90px; height: 50px;
    background: linear-gradient(90deg, var(--paper), #e6e6e6 50%, var(--paper));
  }

  .address {
    position: absolute; right: 48px; top: 738px;
    display: flex; align-items: center; gap: 5px;
    font-family: "Roboto", sans-serif; font-size: 9px; color: var(--ink-dark);
  }
  .address svg { width: 8px; height: 10px; fill: var(--brand-blue); }
</style>
</head>
<body>
  <main class="letterhead">
    <div class="brand">
      <span class="brand-mark"></span>
      <span class="brand-name">Copperline Legal Couriers</span>
    </div>

    <address class="contact">
      <div class="contact-tagline">Process Service and Attorney Support</div>
      <div class="contact-item">
        <svg viewBox="0 0 10 10"><path d="M2 0.5 L4 2.8 L3 4 Q4.5 6 6 7 L7.2 6 L9.5 8 L8 9.5 Q3 9 0.5 2 Z"/></svg>480-555-0142
      </div>
      <div class="contact-item">
        <svg viewBox="0 0 10 10"><rect x="1" y="3" width="8" height="6" rx="1"/><rect x="2.5" y="0.5" width="5" height="3"/></svg>480-555-0178
      </div>
      <div class="contact-item">
        <svg viewBox="0 0 10 10"><path d="M0.5 2 H9.5 V8.5 H0.5 Z M0.5 2 L5 5.5 L9.5 2" stroke="#fff" stroke-width="0.6"/></svg>jordan@copperlinelegal.com
      </div>
      <div class="contact-item">
        <svg viewBox="0 0 10 10"><circle cx="5" cy="5" r="4.5"/><path d="M0.5 5 H9.5 M5 0.5 V9.5" stroke="#fff" stroke-width="0.6"/></svg>www.copperlinelegal.com
      </div>
    </address>

    <div class="watermark" role="img" aria-label="Faint brand decoration"></div>

    <section class="letter-body">
      <div class="salutation">Dear customer,</div>
      <p>Lorem ipsum dolor sit amet, consectetur adipisicing elit, sed do eiusmod tempor incididunt ut labore et dolore magna aliqua. Ut enim ad minim veniam, quis nostrud exercitation ullamco laboris nisi ut aliquip ex ea commodo consequat. Duis aute irure dolor in reprehenderit in voluptate velit esse cillum dolore eu fugiat nulla pariatur. Excepteur sint occaecat cupidatat non proident, sunt in culpa qui officia deserunt mollit anim id est laborum.</p>
      <p>Lorem ipsum dolor sit amet, consectetur adipisicing elit, sed do eiusmod tempor incididunt ut labore et dolore magna aliqua. Ut enim ad minim veniam, quis nostrud exercitation ullamco laboris nisi ut aliquip ex ea commodo consequat. Duis aute irure dolor in reprehenderit in voluptate velit esse cillum dolore eu fugiat nulla pariatur. Excepteur sint occaecat cupidatat non proident, sunt in culpa qui officia deserunt mollit anim id est laborum.</p>
      <p>Lorem ipsum dolor sit amet, consectetur adipisicing elit, sed do eiusmod tempor incididunt ut labore et dolore magna aliqua. Ut enim ad minim veniam, quis nostrud exercitation ullamco laboris nisi ut aliquip ex ea commodo consequat. Duis aute irure dolor in reprehenderit in voluptate velit esse cillum dolore eu fugiat nulla pariatur. Excepteur sint occaecat cupidatat non proident, sunt in culpa qui officia deserunt mollit anim id est laborum.</p>
      <p>Lorem ipsum dolor sit amet, consectetur adipisicing elit, sed do eiusmod tempor incididunt ut labore et dolore magna aliqua. Ut enim ad minim veniam, quis nostrud exercitation ullamco laboris nisi ut aliquip ex ea commodo consequat. Duis aute irure dolor in reprehenderit.</p>
      <div class="closing">Yours Sincerely,</div>
    </section>

    <div class="signature" role="img" aria-label="Handwritten signature"></div>

    <div class="address">
      <svg viewBox="0 0 8 10"><path d="M4 0 A4 4 0 0 1 8 4 Q8 6 4 10 Q0 6 0 4 A4 4 0 0 1 4 0 Z M4 2.4 A1.6 1.6 0 1 0 4 5.6 A1.6 1.6 0 1 0 4 2.4 Z" fill-rule="evenodd"/></svg>
      1200 E Mesa Ridge Rd STE 40 Tempe AZ 85281
    </div>
  </main>
</body>
</html>
```